Fern Lattice Table & Chair Rentals

We need a business card for a table and chair rental company. We rent tables and chairs for weddings, funerals, business events and parties. We want something that looks clean and elegant while not being too busy. We would like colors in the green and blue hues and avoiding anything orange. We want to make sure the font is large enough to be seen easily.

Target Market(s)

Wedding & Event Rentals

Industry/Entity Type

Events

Contact Information for Business Card

Fern Lattice, sales@fernlatticerentals.com, fernlatticerentals.com, 360-555-0182

Requirements
Must have
• Easy to read font
Should not have
• Orange anywhere in the design

```html
<!DOCTYPE html>
<html lang="en">
<head>
<meta charset="utf-8">
<title>Fern Lattice – Business Card</title>
<link rel="stylesheet" href="https://fonts.googleapis.com/css2?family=Arimo:wght@400;700&display=swap">
<style>
  :root {
    --page-bg: #e9e8e4;
    --card-white: #fbfbf9;
    --card-shade: #efefeb;
    --ink: #2f2a1e;
    --ink-soft: #5d584c;
    --accent-sage: #8fae8a;
    --photo-light: #eef1ea;
    --photo-mid: #dbe4d3;
    --photo-green: #b9caa6;
  }
  * { box-sizing: border-box; margin: 0; padding: 0; }
  html, body {
    width: 1200px;
    height: 818px;
    overflow: hidden;
    background: var(--page-bg);
  }
  .canvas {
    width: 1200px;
    height: 818px;
    display: flex;
    align-items: center;
    justify-content: center;
  }
  .business-card {
    width: 1000px;
    height: 572px;
    display: flex;
    background: var(--card-white);
    box-shadow: 0 10px 30px rgba(0,0,0,0.18);
    overflow: hidden;
  }
  .card-photo {
    width: 408px;
    height: 100%;
    background: linear-gradient(180deg, var(--photo-light) 0%, var(--photo-mid) 60%, var(--photo-green) 100%);
  }
  .accent-rule {
    width: 14px;
    height: 100%;
    background: linear-gradient(90deg, var(--card-white) 0 3px, var(--accent-sage) 3px 11px, var(--card-white) 11px);
  }
  .card-info {
    flex: 1;
    padding: 44px 40px 40px 54px;
    background:
      repeating-linear-gradient(90deg, var(--card-white) 0 70px, var(--card-shade) 70px 74px, var(--card-white) 74px 140px);
    font-family: "Arimo", Arial, sans-serif;
    color: var(--ink);
  }
  .brand-name {
    font-size: 44px;
    font-weight: 400;
    line-height: 1.05;
  }
  .brand-tagline {
    margin-top: 6px;
    font-size: 25px;
    color: var(--ink-soft);
  }
  .company-name {
    margin-top: 30px;
    font-size: 50px;
    font-weight: 700;
  }
  .contact-phone {
    margin-top: 24px;
    font-size: 36px;
  }
  .contact-email {
    margin-top: 14px;
    font-size: 25px;
  }
  .contact-web {
    margin-top: 10px;
    font-size: 27px;
  }
  .contact-location {
    margin-top: 26px;
    font-size: 23px;
  }
</style>
</head>
<body>
  <main class="canvas">
    <article class="business-card">
      <div class="card-photo" role="img" aria-label="Photo of a white rose and hydrangea bouquet at a wedding aisle"></div>
      <div class="accent-rule"></div>
      <section class="card-info">
        <div class="brand-name">Fern Lattice</div>
        <div class="brand-tagline">Table and Chair Rentals</div>
        <div class="company-name">Fern Lattice</div>
        <div class="contact-phone">360-555-0182</div>
        <div class="contact-email">sales@fernlatticerentals.com</div>
        <div class="contact-web">www.fernlatticerentals.com</div>
        <div class="contact-location">Cedar Bay, Washington</div>
      </section>
    </article>
  </main>
</body>
</html>
```